Specialised investor in e-mobility and energy wants business card design

We need a business card design that fits our existing corporate design. <The look and feel must be 'sharp'/'clean', dynamic, communicate momentum, professionalism etc (as one would imagine from a firm in the financial sector). We like the idea of a reverse-side of the card that includes the logo, and the name and contact details on the other. We expect the deliverable to be whatever format might be required to be able to get cards printed directly by a service such as kelmo press. Our website is www.zub.capital

```html
<!DOCTYPE html>
<html lang="en">
<head>
<meta charset="utf-8">
<title>Zub Capital – Business Card</title>
<link rel="stylesheet" href="https://fonts.googleapis.com/css2?family=Montserrat:wght@400;500;700;800&display=swap">
<style>
  :root {
    --bg: #2c2e31;
    --card-white: #ffffff;
    --green-dark: #2f5223;
    --green-mid: #3b6b2a;
    --green-bright: #6cb33f;
    --text-grey: #555a57;
    --faint: #ececec;
  }
  * { box-sizing: border-box; margin: 0; padding: 0; }
  html, body { width: 1200px; height: 952px; overflow: hidden; }
  body {
    background: var(--bg);
    font-family: "Montserrat", sans-serif;
    display: flex;
    flex-direction: column;
    align-items: center;
    justify-content: center;
    gap: 48px;
  }
  .card {
    position: relative;
    width: 640px;
    height: 366px;
    border-radius: 22px;
    overflow: hidden;
    box-shadow: 0 10px 30px rgba(0,0,0,.35);
  }

  /* Front */
  .card--front { background: var(--card-white); }
  .brand {
    position: absolute;
    top: 42px;
    left: 250px;
    font-weight: 500;
    font-size: 46px;
    letter-spacing: 1px;
    color: var(--green-dark);
  }
  .person { position: absolute; top: 120px; left: 44px; }
  .person__name {
    font-weight: 800;
    font-size: 24px;
    letter-spacing: .5px;
    color: var(--green-dark);
  }
  .person__role {
    font-size: 14px;
    color: var(--text-grey);
    margin-top: 2px;
  }
  .person__rule {
    width: 70px;
    height: 2px;
    background: var(--green-bright);
    margin-top: 8px;
  }
  .contacts {
    position: absolute;
    top: 218px;
    left: 44px;
    display: grid;
    grid-template-columns: 220px 240px;
    row-gap: 10px;
    column-gap: 20px;
  }
  .contact {
    display: flex;
    align-items: center;
    gap: 10px;
    font-size: 13px;
    color: var(--text-grey);
  }
  .contact__icon {
    width: 20px; height: 20px;
    border-radius: 4px;
    background: var(--green-bright);
    display: flex; align-items: center; justify-content: center;
    flex-shrink: 0;
  }
  .accent-line {
    position: absolute;
    left: 0; top: 300px;
    width: 380px; height: 2px;
    background: var(--green-bright);
  }
  .accent-bar {
    position: absolute;
    left: 380px; top: 296px;
    width: 80px; height: 10px;
    background: var(--green-dark);
  }
  .faint-mark {
    position: absolute;
    left: 478px; top: 274px;
    font-weight: 500;
    font-size: 46px;
    letter-spacing: 2px;
    color: var(--faint);
  }
  .corner-bar {
    position: absolute;
    right: 0; bottom: 30px;
    width: 38px; height: 12px;
    background: var(--green-dark);
  }

  /* Back */
  .card--back { background: var(--green-dark); }
  .back-pattern {
    position: absolute; inset: 0;
    background: linear-gradient(135deg, #34592a 0%, #2f5223 50%, #2b4b20 100%);
  }
  .back-brand {
    position: absolute;
    left: 0; right: 0; bottom: 70px;
    text-align: center;
    font-weight: 500;
    font-size: 40px;
    letter-spacing: 4px;
    color: var(--card-white);
  }
</style>
</head>
<body>

  <section class="card card--front" aria-label="Business card front">
    <div class="brand">Zub Capital</div>

    <div class="person">
      <div class="person__name">MARA KELLER</div>
      <div class="person__role">Manager</div>
      <div class="person__rule"></div>
    </div>

    <div class="contacts">
      <div class="contact">
        <span class="contact__icon">
          <svg width="12" height="12" viewBox="0 0 24 24" fill="#fff"><path d="M6.6 10.8a15.1 15.1 0 0 0 6.6 6.6l2.2-2.2a1 1 0 0 1 1-.25 11.4 11.4 0 0 0 3.6.57 1 1 0 0 1 1 1V20a1 1 0 0 1-1 1A17 17 0 0 1 3 4a1 1 0 0 1 1-1h3.5a1 1 0 0 1 1 1c0 1.25.2 2.45.57 3.57a1 1 0 0 1-.25 1z"/></svg>
        </span>+41 79555 0148
      </div>
      <div class="contact">
        <span class="contact__icon">
          <svg width="12" height="12" viewBox="0 0 24 24" fill="#fff"><path d="M12 2a7 7 0 0 0-7 7c0 5.25 7 13 7 13s7-7.75 7-13a7 7 0 0 0-7-7zm0 9.5A2.5 2.5 0 1 1 12 6.5a2.5 2.5 0 0 1 0 5z"/></svg>
        </span>Lausanne, Switzerland
      </div>
      <div class="contact">
        <span class="contact__icon">
          <svg width="12" height="12" viewBox="0 0 24 24" fill="none" stroke="#fff" stroke-width="2.4"><rect x="3" y="5" width="18" height="14" rx="1"/><path d="M3 6l9 7 9-7"/></svg>
        </span>mara@zub.capital
      </div>
      <div class="contact">
        <span class="contact__icon">
          <svg width="12" height="12" viewBox="0 0 24 24" fill="#fff"><path d="M5 3l14 8-6 1.5L16 20l-3 1-3-7.5L5 17z"/></svg>
        </span>www.zub.capital
      </div>
    </div>

    <div class="accent-line"></div>
    <div class="accent-bar"></div>
    <div class="faint-mark">ZUB</div>
    <div class="corner-bar"></div>
  </section>

  <section class="card card--back" aria-label="Business card back">
    <div class="back-pattern" role="img" aria-label="Subtle repeating brand pattern in tonal dark green"></div>
    <div class="back-brand">ZUB</div>
  </section>

</body>
</html>
```